Regional beer Falkmo-Bräu needs new labels for 33cl Beercans

We are looking for a creative and professional design for our 33cl beer can label. The can itself is all black, and the design should be mainly in yellow and black colors to stand out on the store shelf.
The size of the label should be 206 mm x 80 mm

*Details and requirements:*

1. brand identity and target group
- Our brand stands for handcrafted quality with a modern touch.
- The target group is young adults and beer connoisseurs who value unique taste and stylish design.

2. style and aesthetics:*
- The design should be modern and eye-catching, inspired by the labels of Lunda Brauerei Hamburg.
- We prefer a minimalist style with clean lines and contrasts.

3. typography:*
- Use modern, legible fonts.
- Use freely available fonts.
- The brand name and important information should be emphasized.

4. images and graphics
- The logo can be used in its entirety or in individual parts.
- Illustrations or icons that emphasize the uniqueness of our beer are welcome.

5 *Colors:*
- Main colors are yellow and black.
- Accents in other colors are possible, but should be used sparingly.

6th *Legal requirements:*
- The label must provide space for legal information such as alcohol content, origin and barcode.

7 *Technical details
- Final files should be in AI, afdesign or PDF format with a resolution of at least 300 dpi.
- The design should be created in CMYK color model.

8th *Inspiration and references:*
- Examples of labels that we like are those of Lunda Brauerei Hamburg. We like their clear structure and modern look.

9 *Additional information:*
- The bottling date is printed on the can or bottle afterwards.
- Special features of our beer, such as flavor or special ingredients, should be highlighted.

We look forward to your creative suggestions and hope that you will help us to design a label that perfectly represents our brand!

Target Market(s)

The target group is young adults and beer connoisseurs who value unique taste and stylish design.

Industry/Entity Type

Beverage

Colors

Designer to choose colors to be used in the design.

Requirements
Must have
• The design should be modern and eye-catching but minimalist style with clean lines and contrasts. should include the writing falkmo-bräu (attachment)

```html
<!DOCTYPE html>
<html lang="de">
<head>
<meta charset="utf-8">
<title>Falkmo-Bräu – Dosenetikette 33cl</title>
<link href="https://fonts.googleapis.com/css2?family=Oswald:wght@700&family=Bitter:wght@400;800&family=Work+Sans:wght@300&display=swap" rel="stylesheet">
<style>
  :root {
    --backdrop: #ffb600;
    --can-black: #232325;
    --label-gold: #e9b934;
    --brand-white: #f4f4f2;
    --line-grey: #cfcfcf;
  }
  * { margin: 0; padding: 0; box-sizing: border-box; }
  html, body { width: 1200px; height: 1200px; overflow: hidden; }
  body {
    background: var(--backdrop);
    display: flex;
    align-items: center;
    justify-content: center;
  }
  .can-label {
    position: relative;
    width: 1100px;
    height: 427px;
    background: var(--can-black);
    color: var(--label-gold);
  }
  .label-centre {
    position: absolute;
    left: 50%;
    top: 30px;
    transform: translateX(-50%);
    width: 520px;
    text-align: center;
  }
  .brand-name {
    font-family: "Oswald", sans-serif;
    font-weight: 700;
    font-size: 54px;
    line-height: 1;
    letter-spacing: 1px;
    color: var(--brand-white);
    text-transform: uppercase;
    margin-bottom: 18px;
  }
  .verse { margin-bottom: 11px; line-height: 21px; }
  .verse-lead {
    display: block;
    font-family: "Bitter", serif;
    font-weight: 800;
    font-size: 18px;
  }
  .verse-follow {
    display: block;
    font-family: "Bitter", serif;
    font-weight: 400;
    font-size: 17px;
  }
  .divider { display: block; margin: 10px auto 0; }
  .brewery-info, .product-facts {
    position: absolute;
    bottom: 34px;
    font-family: "Work Sans", sans-serif;
    font-weight: 300;
    font-size: 13px;
    line-height: 17px;
    letter-spacing: 0.8px;
  }
  .brewery-info { left: 60px; }
  .product-facts { right: 60px; text-align: right; }
  .product-facts .volume { margin-top: 10px; }
</style>
</head>
<body>
  <section class="can-label" aria-label="Etikette Falkmo-Bräu 33cl">
    <div class="label-centre">
      <h1 class="brand-name">Falkmo-Bräu</h1>
      <p class="verse">
        <span class="verse-lead">Guets Bier wird nid schlächt!</span>
        <span class="verse-follow">Steu’s aber ane dunkle Ort ad Chüeli</span>
      </p>
      <p class="verse">
        <span class="verse-lead">Besser wird’s im Auter de nid</span>
      </p>
      <p class="verse">
        <span class="verse-lead">Jedi Dösli isch äs Unikat.</span>
        <span class="verse-follow">Vo Hand u mit viu Ufwand brauet</span>
      </p>
      <p class="verse">
        <span class="verse-lead">Für Allergiker jeglicher Art.</span>
        <span class="verse-follow">Löt’s besser grad la si</span>
      </p>
      <svg class="divider" width="280" height="34" viewBox="0 0 280 34">
        <line x1="6" y1="24" x2="122" y2="12" stroke="var(--line-grey)" stroke-width="1.3"/>
        <line x1="158" y1="12" x2="274" y2="2" stroke="var(--line-grey)" stroke-width="1.3"/>
        <path d="M2 24 l7 -3 v6 z" fill="var(--line-grey)"/>
        <path d="M278 2 l-7 -3 v6 z" fill="var(--line-grey)"/>
        <circle cx="140" cy="16" r="12" fill="var(--line-grey)" role="img" aria-label="Hopfendolden-Emblem"/>
      </svg>
    </div>

    <address class="brewery-info" style="font-style:normal">
      Brauerei:<br>
      Falkmo-Bräu<br>
      Lindenweg 7<br>
      CH-3412 Moosried<br>
      www.falkmo-bräu.ch
    </address>

    <div class="product-facts">
      Zutaten:<br>
      Wasser, Gerstenmalz<br>
      Hopfen, Hefe
      <div class="volume">Alc. 4,8% vol.&nbsp;&nbsp;&nbsp;33cl</div>
    </div>
  </section>
</body>
</html>
```